Kelvaro.ch is looking for business card letterhead and envelope C5 with WOW effect

We need a strong business card for our company Kelvaro.ch, logo is available. You want a black or dark background on which the logo Stark r% 26 # 252; appears. Letterhead and envelope in C5 format should be in a similar design, but does not have to be We need a strong business card for our company Kelvaro.ch, logo is available. A black or dark background is desired, on which the logo Stark comes across. The letterhead and the envelope in C5 format should have a similar design.

Target Market(s)

Private customers as well as entrepreneurs

Contact Information for Business Card

E-mail: info@kelvaro-example.ch
Web.www.Kelvaro-example.ch
Tel: +41 ( 0 ) 79 482 6037
Adresse:
Lindenweg 14
9406 Tarnbach

Hier kann man Icons verwenden für Email,Tel und Adressse

Font styles to use
Other font styles liked:
• Dubai,bold

Colors

Designer to choose colors to be used in the design.

Requirements
Must have
• WOW effect
Nice to have
• R% 26 # 252; back business card with our service listings. - VEHICLE LABELING - SHOP WINDOW LABELING - STICKERS AND MUCH MORE ... in red color

```html
<!DOCTYPE html>
<html lang="en">
<head>
<meta charset="utf-8">
<title>Kelvaro.ch – Business Card</title>
<link href="https://fonts.googleapis.com/css2?family=Lato:wght@400;700;900&display=swap" rel="stylesheet">
<style>
  :root {
    --backdrop: #3b342f;
    --card: #0a0a0a;
    --ink: #ffffff;
    --accent: #f4c41c;
    --divider: #8c7534;
    --muted: #e9e9e9;
  }
  * { margin: 0; padding: 0; box-sizing: border-box; }
  html, body { width: 1200px; height: 847px; overflow: hidden; }
  body {
    background: var(--backdrop);
    font-family: "Lato", sans-serif;
    position: relative;
  }
  .card {
    position: absolute;
    top: 269px;
    width: 540px;
    height: 309px;
    background: var(--card);
    border-radius: 3px;
    box-shadow: 0 10px 30px rgba(0,0,0,.45);
    overflow: hidden;
  }
  .card--front { left: 40px; }
  .card--back { left: 620px; }

  .front-wordmark {
    position: absolute;
    left: 150px;
    top: 128px;
    font-weight: 900;
    font-size: 52px;
    letter-spacing: 1px;
    color: var(--ink);
  }

  .brand {
    position: absolute;
    left: 40px;
    top: 135px;
    display: flex;
    align-items: center;
    gap: 12px;
  }
  .brand-mark {
    width: 34px;
    height: 34px;
    background: var(--accent);
  }
  .brand-name {
    font-weight: 900;
    font-size: 24px;
    color: var(--ink);
  }

  .divider {
    position: absolute;
    left: 262px;
    top: 70px;
    width: 1px;
    height: 170px;
    background: var(--divider);
  }

  .contact {
    position: absolute;
    left: 286px;
    top: 72px;
    color: var(--muted);
  }
  .contact-name {
    font-weight: 900;
    font-size: 24px;
    color: var(--accent);
    letter-spacing: .5px;
    line-height: 1.1;
  }
  .contact-role {
    font-size: 14px;
    margin-bottom: 10px;
  }
  .contact-address {
    font-size: 14px;
    line-height: 1.3;
    font-style: normal;
    margin-bottom: 8px;
  }
  .contact-list { list-style: none; font-size: 13.5px; }
  .contact-list li {
    display: flex;
    align-items: center;
    gap: 8px;
    line-height: 1.5;
  }
  .contact-list svg { width: 13px; height: 13px; flex: none; }
</style>
</head>
<body>

<section class="card card--front" aria-label="Business card front">
  <div class="front-wordmark">Kelvaro.ch</div>
</section>

<section class="card card--back" aria-label="Business card back">
  <div class="brand">
    <span class="brand-mark"></span>
    <span class="brand-name">Kelvaro.ch</span>
  </div>

  <div class="divider"></div>

  <div class="contact">
    <div class="contact-name">LUKAS BRENNER</div>
    <div class="contact-role">Founder &amp; CEO</div>
    <address class="contact-address">Lindenweg 14<br>9406 Tarnbach</address>
    <ul class="contact-list">
      <li>
        <svg viewBox="0 0 16 16" aria-hidden="true"><path fill="#f4c41c" d="M3.5 1.5l2.5 0 1 3.5-1.7 1.2a8 8 0 0 0 4.5 4.5L11 9l3.5 1v2.5c0 .8-.7 1.5-1.5 1.5A12 12 0 0 1 2 3c0-.8.7-1.5 1.5-1.5z"/></svg>
        +41 ( 0 ) 79 482 6037
      </li>
      <li>
        <svg viewBox="0 0 16 16" aria-hidden="true"><rect x="1" y="3" width="14" height="10" fill="#f4c41c"/><path d="M1 3l7 6 7-6" fill="none" stroke="#0a0a0a" stroke-width="1.3"/></svg>
        info@kelvaro-example.ch
      </li>
      <li>
        <svg viewBox="0 0 16 16" aria-hidden="true"><g fill="none" stroke="#f4c41c" stroke-width="1.3"><circle cx="8" cy="8" r="6.5"/><ellipse cx="8" cy="8" rx="3" ry="6.5"/><path d="M1.5 8h13M2.5 4.8h11M2.5 11.2h11"/></g></svg>
        www.Kelvaro-example.ch
      </li>
    </ul>
  </div>
</section>

</body>
</html>
```